Vardem Web, LLC. is the name of the company that will be an Internet startup working in E-commerce and

We are a new company and going to start the business by hiring people we need. We are on “Hiring Now…” status right now which we like to be displayed on the website homepage.
The website should allow us to start the hiring process with letting people see and apply for jobs posted on the website.

the company logo is attached.

Target Market(s)

Tech Job Seekers, Programmers, iOS and Android Developers, Software engineers, Graphic designers, QA engineers, Customer Service Reps,...

Industry/Entity Type

Internet

Number of Pages Required

5+ page

Font styles to use
Serif
Sans Serif

Colors

Designer to choose colors to be used in the design.

Requirements
Must have
• We need a system to help job seekers to upload the resume and cover letter and fill the required forms and answer some questions on a form designed to evaluate the job seekers and let them know if they fit in the position and should apply for it.
• We also want job seekers to do a Pre-Employment Tests including Aptitude, Personality, and Skills after they qualified for a job which links our website to web-based pre-employment testing services websites like (Talvexa, Plivmark, Quorvane & Associates, Dunholt Assessment, …)

```html
<!DOCTYPE html>
<html lang="en">
<head>
<meta charset="utf-8">
<title>Vardem Web — Hiring Now</title>
<link href="https://fonts.googleapis.com/css2?family=Montserrat:wght@400;500;600;700&family=Open+Sans:wght@400;600;700&family=Roboto+Slab:wght@800&display=swap" rel="stylesheet">
<style>
:root{
  --blue:#2b7fc0;
  --blue-dark:#1f5f94;
  --orange:#f26522;
  --teal:#6cc5cc;
  --ink:#222;
  --text:#666;
  --muted:#999;
  --line:#e4e4e4;
  --soft:#f7f7f7;
  --white:#fff;
  --dark:#2b2b2b;
}
*{box-sizing:border-box;margin:0;padding:0}
html,body{width:1200px;height:2885px;overflow:hidden}
body{font-family:"Open Sans",sans-serif;color:var(--text);background:var(--white);position:relative}
section,header,footer{position:relative;width:1200px}
.abs{position:absolute}

/* header */
.site-header{height:125px}
.brand{left:130px;top:34px;display:flex;align-items:center;gap:10px}
.brand-name{font-family:"Montserrat",sans-serif;font-weight:700;font-size:38px;color:var(--blue)}
.brand-dot{width:14px;height:14px;background:var(--orange)}
.phone{left:672px;top:36px;font-size:12px;color:var(--muted);display:flex;align-items:center;gap:6px}
.phone b{font-family:"Montserrat",sans-serif;color:var(--blue);font-size:17px;font-weight:600}
.btn{display:inline-block;border:1.5px solid var(--orange);color:var(--orange);font-family:"Montserrat",sans-serif;font-size:13px;font-weight:500;padding:10px 14px;background:var(--white);border-radius:2px}
.btn-tests{left:874px;top:24px;width:180px;text-align:center}
.main-nav{left:438px;top:86px;display:flex;gap:26px;font-family:"Montserrat",sans-serif;font-size:13px;color:#333;align-items:center}

/* hero */
.hero{height:520px;background:linear-gradient(100deg,#eef2f5 0%,#dfe6ec 35%,#5b6f86 60%,#2f3d52 80%,#6f7f90 100%)}
.hero-photo{position:absolute;left:360px;top:0;width:840px;height:520px;background:linear-gradient(90deg,rgba(238,242,245,0) 0%,rgba(60,80,110,.35) 50%,rgba(30,40,60,.4) 100%)}
.hero-title{left:130px;top:148px;font-family:"Roboto Slab",serif;font-weight:800;font-size:58px;color:var(--blue);letter-spacing:1px}
.hero-lede{left:130px;top:222px;width:370px;text-align:center;font-size:17px;font-weight:600;color:#222;line-height:28px}
.hero-actions{left:133px;top:317px;display:flex;gap:30px}
.hero-actions .btn{font-size:13px;padding:10px 16px;display:flex;gap:6px;align-items:center}
.hero-arrows{right:125px;top:435px;display:flex;gap:12px}
.circle-arrow{width:24px;height:24px;border:1.5px solid #ddd;border-radius:50%}

/* welcome */
.welcome{height:488px}
.sec-title{font-family:"Montserrat",sans-serif;font-size:28px;color:var(--ink);font-weight:400;letter-spacing:.5px}
.sec-title b{font-weight:700}
.welcome .sec-title{left:130px;top:68px}
.welcome-copy{left:130px;top:124px;width:578px;font-size:11.5px;line-height:24px;color:#777}
.welcome-copy p+p{margin-top:26px}
.welcome .btn-more{left:130px;top:362px}
.form-card{left:795px;top:68px;width:272px;height:347px;background:var(--soft);box-shadow:0 6px 14px rgba(0,0,0,.14);border:1px solid #ececec;padding:20px 26px}
.form-card h3{font-family:"Montserrat",sans-serif;font-weight:500;font-size:17px;color:#333;text-align:center;margin-bottom:14px}
.field{height:30px;background:var(--white);border:1px solid #e8e8e8;margin-bottom:10px;font-size:10px;color:#888;padding:8px 10px;display:flex;justify-content:space-between}
.form-card .btn{display:block;width:130px;margin:22px auto 0;text-align:center}

/* categories */
.categories{height:522px;background:var(--soft);border-top:1px solid #eee}
.categories .sec-title{width:100%;text-align:center;top:82px}
.cat-grid{left:130px;top:218px;width:937px;height:210px;display:flex;background:var(--white);border:1px solid #ececec}
.cat-card{flex:1;border-right:1px solid #ececec;text-align:center;position:relative;padding-top:76px}
.cat-card:last-child{border-right:0}
.cat-icon{position:absolute;left:50%;top:-58px;margin-left:-58px}
.cat-card h4{font-family:"Montserrat",sans-serif;font-weight:500;font-size:15px;color:#333;margin-bottom:10px}
.cat-card p{font-size:11px;line-height:19px;color:#777;padding:0 28px}
.cat-card a{display:block;margin-top:12px;font-size:10px;font-weight:700;color:var(--orange)}

/* stats */
.stats{height:500px}
.monitor{left:130px;top:86px}
.stats .sec-title{left:545px;top:118px}
.stat-box{left:545px;width:522px;height:118px;border:1px solid #e2e2e2;border-radius:3px;box-shadow:0 2px 4px rgba(0,0,0,.06);padding:14px 22px}
.stat-head{display:flex;justify-content:space-between;font-family:"Open Sans",sans-serif;font-weight:700;font-size:15px;color:#222}
.stat-head span{font-weight:400;font-size:12px;color:#555}
.bar{height:6px;background:#ddd;margin:8px 0 10px}
.bar i{display:block;width:70%;height:100%;background:var(--blue)}
.stat-box p{font-size:10.5px;line-height:18px;color:#555;width:450px}
.stat-box a{position:absolute;right:12px;bottom:8px;font-size:10px;color:var(--orange);text-decoration:underline;font-style:italic}

/* reviews */
.reviews{height:398px;background:linear-gradient(90deg,#3a3a3a,#2a2a2a 45%,#3d3d3d 70%,#555 100%)}
.reviews .sec-title{width:100%;text-align:center;top:78px;color:var(--white);font-weight:700;font-size:24px}
.review{top:150px;width:290px}
.avatar{position:absolute;left:0;top:0;width:68px;height:68px;border-radius:50%;border:3px solid var(--white);background:linear-gradient(#c9b6a8,#8d7a6e)}
.review blockquote{position:absolute;left:84px;top:4px;width:210px;font-size:11px;line-height:20px;font-style:italic;color:#ddd}
.review blockquote b{color:var(--white);font-size:18px;margin-right:4px}
.review h5{position:absolute;left:84px;top:96px;font-family:"Montserrat",sans-serif;font-weight:700;font-size:12px;color:var(--white)}
.review small{position:absolute;left:84px;top:114px;font-size:10px;font-style:italic;color:#ccc}
.stars{position:absolute;left:84px;top:140px;display:flex;gap:3px}
.rev-arrow{top:212px;width:34px;height:34px;border:1.5px solid rgba(255,255,255,.6);border-radius:50%}

/* footer */
.site-footer{height:332px}
.foot-brand{left:130px;top:132px;display:flex;gap:10px;align-items:center}
.foot-brand .brand-name{font-size:40px}
.foot-col{top:46px}
.foot-col h4{font-family:"Montserrat",sans-serif;font-weight:500;font-size:15px;color:#222;margin-bottom:22px}
.foot-col ul{list-style:none;font-size:11px;color:#555;line-height:23px}
.news p{font-size:11px;line-height:18px;color:#555;width:200px}
.news .email{width:238px;height:34px;border:1px solid #ccc;margin-top:14px;font-size:11px;color:#aaa;padding:9px 12px}
.news .btn{margin-top:14px;width:130px;text-align:center}
.contact li{display:flex;gap:14px;margin-bottom:16px;line-height:20px}
.foot-bottom{left:130px;top:272px;width:937px;border-top:1px solid var(--line);padding-top:14px;display:flex;justify-content:space-between;align-items:center;font-size:11px;color:#555}
.socials{display:flex;gap:8px;align-items:center}
.socials i{width:26px;height:26px;border:1.5px solid var(--blue);border-radius:50%;display:block}
</style>
</head>
<body>

<header class="site-header">
  <div class="abs brand"><span class="brand-name">Vardem Web</span><span class="brand-dot"></span></div>
  <div class="abs phone">
    <svg width="14" height="14" viewBox="0 0 24 24"><path fill="#2b7fc0" d="M6.6 10.8a15 15 0 0 0 6.6 6.6l2.2-2.2c.3-.3.7-.4 1-.2 1.1.4 2.3.6 3.6.6.6 0 1 .4 1 1V20c0 .6-.4 1-1 1A17 17 0 0 1 3 4c0-.6.4-1 1-1h3.5c.6 0 1 .4 1 1 0 1.3.2 2.5.6 3.6.1.3 0 .7-.2 1z"/></svg>
    Phone : <b>1.555.014.2290</b>
  </div>
  <a class="abs btn btn-tests">Pre-Employment Tests</a>
  <nav class="abs main-nav">
    <span>Home</span><span>About Us</span><span>Services</span><span>Job Seekers</span><span>Testimonials</span><span>Blog</span><span>Contact Us</span>
    <svg width="14" height="14" viewBox="0 0 24 24"><circle cx="10" cy="10" r="7" fill="none" stroke="#999" stroke-width="2"/><path d="M15 15l6 6" stroke="#999" stroke-width="2"/></svg>
  </nav>
</header>

<section class="hero">
  <div class="hero-photo" role="img" aria-label="Photo of two smiling businessmen in suits working at a laptop"></div>
  <h1 class="abs hero-title">HIRING NOW</h1>
  <p class="abs hero-lede">Exercitation ullamco laboris nisi ut aliquip commodo consequat irure...</p>
  <div class="abs hero-actions">
    <a class="btn"><svg width="12" height="12" viewBox="0 0 24 24"><path fill="#f26522" d="M10 3h4v9h4l-6 6-6-6h4zM4 19h16v3H4z"/></svg>Upload The Resume</a>
    <a class="btn" style="border-color:var(--blue);color:var(--blue)"><svg width="12" height="12" viewBox="0 0 24 24"><path fill="#2b7fc0" d="M10 21h4v-9h4l-6-6-6 6h4zM4 2h16v3H4z"/></svg>Cover Letter</a>
  </div>
  <div class="abs hero-arrows"><span class="circle-arrow"></span><span class="circle-arrow"></span></div>
</section>

<section class="welcome">
  <h2 class="abs sec-title">WELCOME TO <b>VARDEM</b></h2>
  <div class="abs welcome-copy">
    <p>Eiusmod tempor incididunt ut labore et dolore magna aliqua. Ut enim ad minim veniam, quis nostrud exercition ullamco laboris nisi ut aliquip ex ea commodo consequat. Duis aute irure dolor in reprehenderit in voluptate velit esse cillum dolore eu fugiat nulla pariatur</p>
    <p>Eiusmod tempor incididunt ut labore et dolore magna aliqua. Ut enim ad minim veniam, quis nostrud exercition ullamco laboris nisi ut aliquip ex ea commodo consequat. Duis aute irure dolor in reprehenderit in voluptate velit esse cillum dolore eu fugiat nulla pariatur sint occaecat cupidatat non proident, sunt in culpa qui officia deserunt mollit anim id est laborum...</p>
  </div>
  <a class="abs btn btn-more">Read More info</a>
  <form class="abs form-card">
    <h3>REQUIRED FORMS</h3>
    <div class="field">Name</div>
    <div class="field">Email</div>
    <div class="field">Job Title<span>⌄</span></div>
    <div class="field">Location<span>⌄</span></div>
    <div class="field">Company Name</div>
    <a class="btn">Click to Apply</a>
  </form>
</section>

<section class="categories">
  <h2 class="abs sec-title">JOB <b>CATEGORIES</b></h2>
  <div class="abs cat-grid">
    <div class="cat-card">
      <svg class="cat-icon" width="116" height="116" viewBox="0 0 116 116"><path d="M62 8a50 50 0 0 1 30 90l-14-8a40 40 0 0 0-16-82z" fill="var(--teal)"/><circle cx="54" cy="58" r="42" fill="var(--blue)" stroke="#fff" stroke-width="4"/><rect x="38" y="44" width="32" height="22" fill="none" stroke="#fff" stroke-width="2.5"/><path d="M48 72h12M54 66v6" stroke="#fff" stroke-width="2.5"/></svg>
      <h4>Eiusmod Tempor</h4><p>Excepteur sint occaecat cupidatat non proident, sunt in culpa qui deserunt mollit anim id laborum...</p><a>READ MORE &gt;&gt;</a>
    </div>
    <div class="cat-card">
      <svg class="cat-icon" width="116" height="116" viewBox="0 0 116 116"><path d="M62 8a50 50 0 0 1 30 90l-14-8a40 40 0 0 0-16-82z" fill="var(--teal)"/><circle cx="54" cy="58" r="42" fill="var(--blue)" stroke="#fff" stroke-width="4"/><path d="M36 52l10-8 8 6 8-6 10 8-12 12-6-4-6 4z" fill="none" stroke="#fff" stroke-width="2.5" stroke-linejoin="round"/></svg>
      <h4>Eiusmod Tempor</h4><p>Excepteur sint occaecat cupidatat non proident, sunt in culpa qui deserunt mollit anim id laborum...</p><a>READ MORE &gt;&gt;</a>
    </div>
    <div class="cat-card">
      <svg class="cat-icon" width="116" height="116" viewBox="0 0 116 116"><path d="M62 8a50 50 0 0 1 30 90l-14-8a40 40 0 0 0-16-82z" fill="var(--teal)"/><circle cx="54" cy="58" r="42" fill="var(--blue)" stroke="#fff" stroke-width="4"/><rect x="42" y="40" width="24" height="32" fill="none" stroke="#fff" stroke-width="2.5"/><path d="M47 50h14M47 56h14M47 62h10" stroke="#fff" stroke-width="2"/></svg>
      <h4>Eiusmod Tempor</h4><p>Excepteur sint occaecat cupidatat non proident, sunt in culpa qui deserunt mollit anim id laborum...</p><a>READ MORE &gt;&gt;</a>
    </div>
    <div class="cat-card">
      <svg class="cat-icon" width="116" height="116" viewBox="0 0 116 116"><path d="M62 8a50 50 0 0 1 30 90l-14-8a40 40 0 0 0-16-82z" fill="var(--teal)"/><circle cx="54" cy="58" r="42" fill="var(--blue)" stroke="#fff" stroke-width="4"/><path d="M42 68h24l-3-5V53a9 9 0 0 0-18 0v10z" fill="none" stroke="#fff" stroke-width="2.5" stroke-linejoin="round"/><circle cx="54" cy="72" r="3" fill="#fff"/></svg>
      <h4>Eiusmod Tempor</h4><p>Excepteur sint occaecat cupidatat non proident, sunt in culpa qui deserunt mollit anim id laborum...</p><a>READ MORE &gt;&gt;</a>
    </div>
  </div>
</section>

<section class="stats">
  <svg class="abs monitor" width="325" height="345" viewBox="0 0 325 345">
    <rect x="0" y="0" width="325" height="240" rx="6" fill="#111"/>
    <rect x="14" y="14" width="297" height="212" fill="#cfe3ef" role="img" aria-label="Photo of a young businessman holding a tablet"/>
    <rect x="0" y="240" width="325" height="34" fill="#e6e6e6"/>
    <path d="M130 274h66l10 52h-86z" fill="#d4d4d4"/>
    <ellipse cx="163" cy="330" rx="70" ry="6" fill="#e0e0e0"/>
  </svg>
  <h2 class="abs sec-title">JOB <b>STATISTICS</b></h2>
  <div class="abs stat-box" style="top:160px">
    <div class="stat-head">Tempor Lincididunt 123.989.999 labore<span>70%</span></div>
    <div class="bar"><i></i></div>
    <p>Pre-trial settlement for local client who broke his femur in a collision on his way to work after evidence of gross negligence was uncovered.</p>
    <a>Apply Now</a>
  </div>
  <div class="abs stat-box" style="top:297px">
    <div class="stat-head">Tempor Lincididunt 123.989.999 labore<span>70%</span></div>
    <div class="bar"><i></i></div>
    <p>Pre-trial settlement for local client who broke his femur in a collision on his way to work after evidence of gross negligence was uncovered.</p>
    <a>Apply Now</a>
  </div>
</section>

<section class="reviews" role="img" aria-label="Dim office photo of a businessman with a tablet behind the reviews">
  <h2 class="abs sec-title">CUSTOMER REVIEWS</h2>
  <span class="abs rev-arrow" style="left:68px"></span>
  <span class="abs rev-arrow" style="right:68px"></span>
  <div class="abs review" style="left:130px">
    <span class="avatar" role="img" aria-label="Reviewer portrait"></span>
    <blockquote><b>“</b>At vero eos et accusamus et iustodio dignissimos ducimus qui blanditiipraesnt ium voluptatum deleniti atq.</blockquote>
    <h5>MARLA QUENBY</h5><small>Lorem ipsum dolor sit amet dummy</small>
    <div class="stars"><svg width="90" height="16" viewBox="0 0 90 16"><g fill="#f5c518"><path id="s" d="M8 1l2 5h5l-4 3 2 6-5-4-5 4 2-6-4-3h5z"/><use href="#s" x="18"/><use href="#s" x="36"/><use href="#s" x="54"/></g><use href="#s" x="72" fill="none" stroke="#f5c518"/></svg></div>
  </div>
  <div class="abs review" style="left:455px">
    <span class="avatar" role="img" aria-label="Reviewer portrait" style="background:linear-gradient(#bbb,#666)"></span>
    <blockquote><b>“</b>At vero eos et accusamus et iustodio dignissimos ducimus qui blanditiipraesnt ium voluptatum deleniti atq.</blockquote>
    <h5>MARLA QUENBY</h5><small>Lorem ipsum dolor sit amet dummy</small>
    <div class="stars"><svg width="90" height="16" viewBox="0 0 90 16"><g fill="#f5c518"><use href="#s"/><use href="#s" x="18"/><use href="#s" x="36"/><use href="#s" x="54"/><use href="#s" x="72"/></g></svg></div>
  </div>
  <div class="abs review" style="left:780px">
    <span class="avatar" role="img" aria-label="Reviewer portrait" style="background:linear-gradient(#e3d6cc,#a59286)"></span>
    <blockquote><b>“</b>At vero eos et accusamus et iustodio dignissimos ducimus qui blanditiipraesnt ium voluptatum deleniti atq.</blockquote>
    <h5>MARLA QUENBY</h5><small>Lorem ipsum dolor sit amet dummy</small>
    <div class="stars"><svg width="90" height="16" viewBox="0 0 90 16"><g fill="#f5c518"><use href="#s"/><use href="#s" x="18"/><use href="#s" x="36"/><use href="#s" x="54"/></g><use href="#s" x="72" fill="none" stroke="#f5c518"/></svg></div>
  </div>
</section>

<footer class="site-footer">
  <div class="abs foot-brand"><span class="brand-name">Vardem Web</span><span class="brand-dot"></span></div>
  <div class="abs foot-col" style="left:432px">
    <h4>Quick Links</h4>
    <ul><li>Home</li><li>About us</li><li>Services</li><li>Job Seekers</li><li>Blog</li><li>Contact Us</li></ul>
  </div>
  <div class="abs foot-col news" style="left:587px">
    <h4>Newsletter Subscription</h4>
    <p>Register your Email Address to get information about us</p>
    <div class="email">Email Address</div>
    <a class="btn">Subscribe</a>
  </div>
  <div class="abs foot-col contact" style="left:888px">
    <h4>Contact Us</h4>
    <ul>
      <li><svg width="12" height="14" viewBox="0 0 24 28"><path fill="#2b7fc0" d="M12 0a10 10 0 0 0-10 10c0 8 10 18 10 18s10-10 10-18A10 10 0 0 0 12 0zm0 14a4 4 0 1 1 0-8 4 4 0 0 1 0 8z"/></svg><span>Box 5120<br>40217 Norvik, Eastmere</span></li>
      <li><svg width="12" height="14" viewBox="0 0 24 24"><path fill="#2b7fc0" d="M6.6 10.8a15 15 0 0 0 6.6 6.6l2.2-2.2c.3-.3.7-.4 1-.2 1.1.4 2.3.6 3.6.6.6 0 1 .4 1 1V20c0 .6-.4 1-1 1A17 17 0 0 1 3 4c0-.6.4-1 1-1h3.5c.6 0 1 .4 1 1 0 1.3.2 2.5.6 3.6.1.3 0 .7-.2 1z"/></svg><span>1 555 014 2290</span></li>
      <li><svg width="12" height="14" viewBox="0 0 24 20"><rect width="24" height="18" fill="#2b7fc0"/><path d="M1 1l11 9 11-9" fill="none" stroke="#fff" stroke-width="2"/></svg><span>info@vardemweb.com</span></li>
    </ul>
  </div>
  <div class="abs foot-bottom">
    <span>Copyright © 2017, Vardem Web. All rights reserved.</span>
    <div class="socials"><i></i><i></i><i></i><i></i><span style="margin-left:10px">C11</span></div>
  </div>
</footer>

</body>
</html>
```